Tavenhurst Falcons FC Website

We are looking to develop a new website for Tavenhurst FC. Tavenhurst FC has now joined with Tavenhurst Falcons FC and we are looking at a website that can work for both clubs. Tavenhurst FC play in a local park football competition while tavenhurst Falcons are a Semi Professional team that plays in the Ostral Premier Series Competition. What we are after is two separate website off the one platform. I have attached both team logos for you to visualise. Also you can look at the existing tavenhurst website www.tavenhurstfc.net.au. We are looking for a huge improvement in the website and it will be imperative we have links to sponsors and the sponsors can get regular visuals. Weare looking to move this club forward and have a very professional website that can communicate clearly with the community.

Hi All,

Please remember that the website is to represent two clubs;
1. Tavenhurst Falcons FC (Competes in Semi Professional League)
2. Tavenhurst FC (Compete in KPWLT League which is a lower level)

Further to this the Tavenhurst Falcons FC page will require a player profile page which will show photos of each player and a little bio on each.

Thanks

Reason: Would like to spend more time review existing and new designs

```html
<!DOCTYPE html>
<html lang="en">
<head>
<meta charset="utf-8">
<title>Tavenhurst FC</title>
<link href="https://fonts.googleapis.com/css2?family=Exo+2:wght@300;400;500;600&family=Open+Sans:wght@400;600&display=swap" rel="stylesheet">
<style>
:root{
  --red:#c8161d;
  --red-dark:#9e0f14;
  --ink:#2b2b2b;
  --grey:#8a8a8a;
  --light:#f1f1f1;
  --line:#3a3a3a;
  --footer:#1e1e1e;
  --footer-text:#9a9a9a;
  --white:#ffffff;
}
*{margin:0;padding:0;box-sizing:border-box}
html,body{width:1200px;height:2416px;overflow:hidden}
body{position:relative;background:var(--white);font-family:"Open Sans",Arial,sans-serif;color:var(--ink)}
.abs{position:absolute}
.display{font-family:"Exo 2",Arial,sans-serif}

/* hero */
.hero{left:0;top:0;width:1200px;height:557px;background:linear-gradient(120deg,#3a2f24 0%,#8b7458 35%,#c9b08a 55%,#6d5a44 80%,#2e2720 100%)}
.nav{left:0;top:35px;width:1200px;height:57px;background:var(--white);box-shadow:0 1px 3px rgba(0,0,0,.15)}
.nav a{position:absolute;top:21px;font-family:"Exo 2",sans-serif;font-size:13.5px;font-weight:500;color:var(--ink);text-decoration:none;letter-spacing:.2px}
.nav a.active{color:var(--red)}
.nav a.active::after{content:"";position:absolute;left:-14px;right:-14px;top:35px;height:3px;background:var(--red)}
.brand{left:543px;top:0;width:114px;height:130px;background:var(--white);border-radius:0 0 57px 57px;box-shadow:0 2px 6px rgba(0,0,0,.25);display:flex;align-items:center;justify-content:center;text-align:center;font-family:"Exo 2",sans-serif;font-weight:600;font-size:15px;line-height:1.1;color:var(--red)}
.arrow{width:44px;height:44px;border-radius:50%;border:2px solid var(--white);top:281px}
.arrow.prev{left:67px}
.arrow.next{left:1090px;border-color:var(--red)}
.hero-mark{left:161px;top:333px;width:110px;height:110px;border-radius:50%;background:var(--red);opacity:.9}
.hero-title{left:293px;top:326px;font-size:42px;font-weight:500;color:var(--red);letter-spacing:1px}
.hero-text{left:294px;top:381px;width:350px;font-size:13px;line-height:20px;color:var(--white)}

/* welcome */
.welcome{left:0;top:557px;width:1200px;height:276px;background:linear-gradient(180deg,#ececec,#f4f4f4)}
.welcome h1{position:absolute;left:161px;top:37px;font-family:"Exo 2",sans-serif;font-weight:400;font-size:43px;line-height:46px;color:var(--ink)}
.welcome h1 span{color:var(--red)}
.register{left:161px;top:147px;width:277px;height:77px;background:linear-gradient(180deg,var(--red),var(--red-dark));color:var(--white);padding:14px 0 0 76px;font-family:"Exo 2",sans-serif}
.register small{display:block;font-size:16px;font-variant:small-caps}
.register strong{display:block;font-size:22px;font-weight:500}
.welcome h2{position:absolute;left:491px;top:56px;width:548px;padding-bottom:10px;border-bottom:2px solid var(--line);font-family:"Exo 2",sans-serif;font-weight:400;font-size:24px;letter-spacing:1px}
.welcome h2 span{color:var(--red)}
.welcome p{position:absolute;left:491px;top:117px;width:548px;font-size:13px;line-height:20px;color:var(--grey)}

/* fixtures */
.fixtures{left:0;top:833px;width:1200px;height:525px;background:var(--white)}
.section-title{font-family:"Exo 2",sans-serif;font-weight:400;font-size:32px;color:var(--red);letter-spacing:1px}
.fixtures .section-title{position:absolute;left:161px;top:48px;width:625px;padding-bottom:8px;border-bottom:2px solid var(--line)}
.fixtures .section-title span{color:var(--ink)}
.fixtures p{position:absolute;left:161px;top:125px;width:625px;font-size:13px;line-height:21px;color:var(--grey)}
.fixture-list{position:absolute;top:218px;list-style:none}
.fixture-list li{height:25.8px;font-family:"Exo 2",sans-serif;font-size:15px;color:var(--ink);padding-left:20px;position:relative}
.fixture-list li::before{content:"";position:absolute;left:0;top:6px;width:8px;height:8px;border:2px solid var(--ink)}
.fixture-list li.current{color:var(--red)}
.fixture-list li.current::before{border-color:var(--red)}
.player{left:830px;top:29px;width:201px;height:491px;background:linear-gradient(180deg,#e8d6c8 0%,#b8232c 25%,#a51d25 60%,#6e1519 100%);border-radius:60px 60px 10px 10px}

/* no smoking */
.notice{left:0;top:1358px;width:1200px;height:232px;background:linear-gradient(180deg,#555 0%,#3f3f3f 50%,#5a5a5a 100%)}
.notice-icon{left:162px;top:44px}
.notice h3{position:absolute;left:385px;top:36px;width:654px;padding-bottom:6px;border-bottom:1px solid rgba(255,255,255,.5);font-family:"Exo 2",sans-serif;font-weight:400;font-size:30px;color:var(--white);letter-spacing:1px}
.notice p{position:absolute;left:385px;top:104px;width:654px;font-size:13px;line-height:20px;color:#e4e4e4}
.btn{display:flex;align-items:center;justify-content:center;background:var(--red);color:var(--white);font-family:"Exo 2",sans-serif;font-size:15px;font-variant:small-caps}
.notice .btn{position:absolute;left:388px;top:158px;width:116px;height:31px}

/* sponsors */
.sponsors{left:0;top:1590px;width:1200px;height:477px;background:var(--light)}
.sponsors .section-title{position:absolute;left:161px;top:48px;width:878px;padding-bottom:8px;border-bottom:2px solid var(--line)}
.sponsor-grid{position:absolute;left:161px;top:134px;width:437px;height:282px;display:grid;grid-template-columns:repeat(3,1fr);grid-template-rows:repeat(3,1fr);gap:2px;background:#e2e2e2;border:2px solid #e2e2e2}
.sponsor-grid div{background:var(--white);display:flex;align-items:center;justify-content:center;font-family:"Exo 2",sans-serif;font-weight:600;font-size:14px;color:var(--ink);text-align:center}
.featured{position:absolute;left:633px;top:150px;font-family:"Exo 2",sans-serif;font-weight:400;font-size:35px;color:#555}
.sponsors p{position:absolute;left:633px;top:201px;width:406px;font-size:13px;line-height:20px;color:var(--grey)}
.sponsors .btn{position:absolute;left:633px;top:367px;width:157px;height:37px}

/* footer */
.footer{left:0;top:2067px;width:1200px;height:349px;background:var(--footer)}
.footer h4{position:absolute;top:51px;font-family:"Exo 2",sans-serif;font-weight:400;font-size:18px;color:#bdbdbd;letter-spacing:.5px}
.sitemap{position:absolute;left:161px;top:90px;width:158px;border-top:1px solid #333;padding-top:13px;list-style:none}
.sitemap li{height:25.8px;font-size:12px;color:var(--footer-text);padding-left:20px;position:relative}
.sitemap li::before{content:"";position:absolute;left:2px;top:6px;width:6px;height:6px;border:1px solid var(--footer-text)}
.news-item{position:absolute;left:425px;width:290px;height:44px}
.news-item .thumb{position:absolute;left:0;top:0;width:58px;height:43px;background:linear-gradient(135deg,#6c6c6c,#3b3b3b)}
.news-item strong{position:absolute;left:68px;top:0;width:180px;font-size:10.5px;line-height:13px;font-weight:600;color:#d4d4d4}
.news-item small{position:absolute;left:68px;top:30px;font-size:9px;color:#777;font-style:italic}
.pager{top:56px;width:14px;height:14px;border-radius:50%;background:#555}
.view-all{left:997px;top:56px;font-size:10px;color:#666}
.gallery{position:absolute;left:780px;top:106px;width:259px;height:118px;display:grid;grid-template-columns:repeat(3,1fr);grid-template-rows:repeat(2,1fr);gap:3px}
.gallery div{background:linear-gradient(135deg,#8a8a8a,#3d3d3d)}
.copyright{left:161px;top:316px;font-size:11px;color:#777}
.social{left:890px;top:306px;display:flex;gap:6px}
.social span{width:26px;height:26px;border-radius:50%;border:1px solid #888}
</style>
</head>
<body>

<section class="abs hero" role="img" aria-label="Photo of a youth football match: a player in yellow striking the ball while a goalkeeper dives"></section>

<nav class="abs nav">
  <a class="active" style="left:177px">HOME</a>
  <a style="left:242px">ABOUT US</a>
  <a style="left:327px">NEWS</a>
  <a style="left:390px">FIXTURE &amp; RESULTS</a>
  <a style="left:685px">PHOTO GALLERY</a>
  <a style="left:809px">SPONSOR</a>
  <a style="left:891px">CLUB</a>
  <a style="left:949px">CONTACT US</a>
</nav>
<div class="abs brand">Tavenhurst<br>FC</div>

<div class="abs arrow prev"><svg width="40" height="40" viewBox="0 0 40 40"><path d="M23 13 L16 20 L23 27" fill="none" stroke="#fff" stroke-width="2.5"/></svg></div>
<div class="abs arrow next"><svg width="40" height="40" viewBox="0 0 40 40"><path d="M17 13 L24 20 L17 27" fill="none" stroke="#c8161d" stroke-width="2.5"/></svg></div>

<div class="abs hero-mark"></div>
<div class="abs hero-title display">TAVENHURST FC</div>
<p class="abs hero-text">Lorem Ipsum is simply dummy text of the printing and typesetting industry. Lorem Ipsum has been the industry's standard dummy text .</p>

<section class="abs welcome">
  <h1>WELCOME TO<br><span>TAVENHURST FC</span></h1>
  <div class="abs register"><small>2014 Season</small><strong>REGISTER ONLINE</strong></div>
  <h2>LET’S TALK <span>ABOUT</span> TAVENHURST FC.</h2>
  <p>Lorem Ipsum is simply dummy text of the printing and typesetting industry. Lorem Ipsum has been the industry's standard dummy text ever since the 1500s, when an unknown printer took a galley of type and scrambled it to make a type specimen book. It has survived not only five centuries, but also the leap into electronic typesetting, remaining essentially unchanged.</p>
</section>

<section class="abs fixtures">
  <h2 class="section-title">FIXTURES <span>&amp;</span> RESULTS</h2>
  <p>Lorem Ipsum is simply dummy text of the printing and typesetting industry. Lorem Ipsum has been the industry's standard dummy text ever since the 1500s, when an unknown printer took a galley of type and scrambled it to make a type specimen book.</p>
  <ul class="fixture-list" style="left:161px">
    <li>PREMIER LEAGUE</li><li class="current">PREMIER LEAGUE RES</li><li>SUPER LEAGUE</li><li>SUPER LEAGUE RES</li><li>UNDER 16 / 2</li><li>UNDER 17 / 1</li><li>UNDER 10 / 2</li><li>UNDER 10 / 3</li><li>UNDER 11 / 1</li><li>UNDER 12 / 3</li>
  </ul>
  <ul class="fixture-list" style="left:424px">
    <li>UNDER 13 / 3</li><li>UNDER 14 / 3</li><li>AA MEN / 5</li><li>AA MEN / 6</li><li>AA MEN / 8</li><li>AA MEN / 10</li><li>AA MEN / 10</li><li>AA MEN / 14</li><li>07 ECL / RED</li><li>07 ECL / GREEN</li>
  </ul>
  <ul class="fixture-list" style="left:656px">
    <li>07 ECL / BLUE</li><li>08 ECL / BLUE</li><li>08 ECL / GREEN</li><li>09 / GREEN</li><li>06 / A GREEN</li><li>06 / B BLUE</li><li>06 / C RED</li><li>06 / D PURPLE</li><li>06 / E WHITE</li><li>06 / F BROWN</li>
  </ul>
  <div class="abs player" role="img" aria-label="Photo of a footballer in a red kit standing with arms crossed beside a ball"></div>
</section>

<section class="abs notice" role="group" aria-label="No smoking notice">
  <svg class="abs notice-icon" width="144" height="144" viewBox="0 0 144 144">
    <circle cx="72" cy="72" r="72" fill="#fff"/>
    <circle cx="72" cy="72" r="54" fill="none" stroke="#1e1e1e" stroke-width="10"/>
    <rect x="38" y="70" width="58" height="12" fill="#1e1e1e"/>
    <rect x="99" y="70" width="6" height="12" fill="#1e1e1e"/>
    <line x1="34" y1="34" x2="110" y2="110" stroke="#1e1e1e" stroke-width="10"/>
  </svg>
  <h3>NO SMOKING</h3>
  <p>Lorem Ipsum is simply dummy text of the printing and typesetting industry. Lorem Ipsum has been the industry's standard dummy text ever since the 1500s.</p>
  <div class="btn">Learn More</div>
</section>

<section class="abs sponsors">
  <h2 class="section-title">OUR SPONSOR</h2>
  <div class="sponsor-grid">
    <div>Brightline Media</div>
    <div>Corwen Lasko &amp; Co</div>
    <div>Ashvale Print</div>
    <div>Pell's</div>
    <div>Kellbrook Motor Group</div>
    <div>Veltrace</div>
    <div>Tavenhurst Bowling Club</div>
    <div>Meridan Bank</div>
    <div>Onyx Auto</div>
  </div>
  <div class="featured">kellbrook motor group</div>
  <p>Lorem Ipsum is simply dummy text of the printing and typesetting industry. Lorem Ipsum has been the industry's standard dummy text ever since the 1500s, when an unknown printer took a galley of type and scrambled it to make a type specimen book. It has survived not only five centuries, but also the leap into electronic typesetting, remaining essentially unchanged. It was popularised in the 1960s with the release of Letraset sheets containing Lorem Ipsum passages.</p>
  <div class="btn">View All Sponsor</div>
</section>

<footer class="abs footer">
  <h4 style="left:161px">SITE MAP</h4>
  <ul class="sitemap">
    <li>Become A Referee</li><li>News</li><li>Fixture &amp; Results</li><li>Photo Gallery</li><li>Sponsor</li><li>Club</li><li>Contact Us</li>
  </ul>

  <h4 style="left:424px">LATEST NEWS</h4>
  <span class="abs pager" style="left:649px"></span>
  <span class="abs pager" style="left:669px"></span>
  <div class="news-item" style="top:108px"><div class="thumb" role="img" aria-label="News photo"></div><strong>Lorem Ipsum is simply dummy text of the typesetting industry.</strong><small>Mar 11, 2014</small></div>
  <div class="news-item" style="top:166px"><div class="thumb" role="img" aria-label="News photo"></div><strong>Lorem Ipsum is simply dummy text of the typesetting industry.</strong><small>Mar 11, 2014</small></div>
  <div class="news-item" style="top:224px"><div class="thumb" role="img" aria-label="News photo"></div><strong>Lorem Ipsum is simply dummy text of the typesetting industry.</strong><small>Mar 11, 2014</small></div>

  <h4 style="left:778px">PHOTO GALLERY</h4>
  <span class="abs view-all">View All</span>
  <div class="gallery">
    <div role="img" aria-label="Club photo"></div><div role="img" aria-label="Club photo"></div><div role="img" aria-label="Club photo"></div>
    <div role="img" aria-label="Club photo"></div><div role="img" aria-label="Club photo"></div><div role="img" aria-label="Club photo"></div>
  </div>

  <p class="abs copyright">Copyright .TAVENHURST FC ® 2014. All rights reserved. Terms and Conditions</p>
  <div class="abs social" aria-label="Social links"><span></span><span></span><span></span><span></span><span></span></div>
</footer>

</body>
</html>
```